Launch Website

A very simple, but attractive website (template preferred) is required in a common format - HTML5 or Wordpress etc.
It should be easily user updateable for updates.
Pages it needs:
-Home Page with menu bar, company logo and 1 large graphic/picture and two smaller graphics/logos.
- What we do
- How we do it
- About Us
- Guarantees
- Results
- Contact Page with Enquiry Form
- Provision for a blog to be added later

Most pages will be approx 150 words text with some small/medium images.
We have our own domain & hosting.

A "less is more" design approach would be encouraged.

Target Market(s)

Vehicle Fleet Managers

Industry/Entity Type

It Company

Font styles to use
Sans Serif

Colors
9bcb3c

Requirements
Must have
• Corporate Style. No Fluff.
Nice to have
• Images of LIght Commerical vehicles and trucks

Am ok with white background throughout site.
Colours should match/complement company logo.
Should not have
• Should not be too "busy"

```html
<!DOCTYPE html>
<html lang="en">
<head>
<meta charset="utf-8">
<title>Northline Diesel</title>
<link href="https://fonts.googleapis.com/css2?family=Open+Sans:wght@400;600&family=Roboto+Condensed:wght@400;700&display=swap" rel="stylesheet">
<style>
:root{
  --brand-green:#1a9a48;
  --navy:#154a7e;
  --navy-dark:#0f3d6a;
  --accent-blue:#1c9ad6;
  --ink:#222;
  --muted:#8a8a8a;
  --rule:#d8d8d8;
  --footer-bg:#eeeeee;
  --button-bg:#c9c9c9;
  --phone-red:#d42020;
  --callout-bg:#0b0b0b;
  --social-blue:#1f5fa0;
}
*{box-sizing:border-box;margin:0;padding:0}
html,body{width:1200px;height:1003px;overflow:hidden;background:#fff}
body{position:relative;font-family:"Open Sans",Arial,sans-serif;color:var(--ink)}

.site-header{position:absolute;left:0;top:0;width:1200px;height:102px;background:linear-gradient(#ffffff,#f0f0f0)}
.brand-name{position:absolute;left:131px;top:28px;font-family:"Open Sans",Arial,sans-serif;font-weight:600;font-size:34px;line-height:40px;color:var(--brand-green);white-space:nowrap}
.phone-icon{position:absolute;left:806px;top:26px}
.contact-block{position:absolute;left:845px;top:26px;font-size:14px;color:#777;line-height:20px;white-space:nowrap}
.contact-block .phone{color:var(--phone-red);font-size:20px}
.contact-block .email{color:#333}

.hero-band{position:absolute;left:0;top:102px;width:1200px;height:442px;background:linear-gradient(var(--navy-dark),var(--navy) 60%,#1a5590)}
.main-nav{position:absolute;left:0;top:102px;width:1200px;height:48px}
.main-nav a{position:absolute;top:15px;transform:translateX(-50%);font-weight:600;font-size:14px;color:#fff;text-decoration:none;white-space:nowrap}

.slider{position:absolute;left:131px;top:155px;width:937px;height:467px;background:#fff;border-radius:3px;box-shadow:0 18px 18px -14px rgba(0,0,0,.35)}
.slide-photo{position:absolute;left:9px;top:9px;width:919px;height:450px;background:linear-gradient(180deg,#6f8a4e 0%,#8fa068 35%,#b7a97c 62%,#d9d6cc 100%)}
.callout{position:absolute;left:543px;top:53px;width:365px;height:178px}
.callout-text{position:absolute;left:70px;top:24px;font-family:"Roboto Condensed",Arial,sans-serif;color:#fff;font-size:23px;line-height:28px}
.callout-text .save{display:block;color:var(--accent-blue);font-size:19px;line-height:22px}
.callout-text .big{display:block;color:var(--accent-blue);font-weight:700;font-size:54px;line-height:50px;letter-spacing:-1px}
.callout-text .big small{font-size:32px;letter-spacing:0}
.callout-text .tail{display:block;margin-left:6px}
.partner-badge{position:absolute;top:365px;height:75px;background:#fff}
.badge-member{left:547px;width:128px}
.badge-partner{left:685px;width:224px}
.badge-member span{position:absolute;left:18px;top:14px;width:92px;height:46px;background:#b9c2cc;border-radius:4px}
.badge-partner span{position:absolute;left:12px;top:18px;width:200px;height:40px;background:#2a2a2a;border-radius:20px}
.slider-dots{position:absolute;left:20px;top:430px;display:flex;gap:3px}
.slider-dots i{width:10px;height:10px;background:#fff}
.slider-dots i.active{background:var(--accent-blue)}

.features{position:absolute;left:131px;top:680px;width:938px}
.feature{position:absolute;top:0;width:206px}
.feature h2{font-family:"Roboto Condensed",Arial,sans-serif;font-weight:400;font-size:20px;color:var(--accent-blue);height:34px;border-bottom:1px solid var(--rule);position:relative}
.feature h2::after{content:"";position:absolute;left:0;bottom:-2px;width:84px;height:3px;background:var(--accent-blue)}
.feature p{margin-top:20px;font-size:12.3px;line-height:18.7px;color:var(--muted);height:94px}
.read-more{position:absolute;top:161px;left:0;width:77px;height:24px;background:var(--button-bg);color:#fff;font-size:11.5px;line-height:24px;text-align:center;text-decoration:none;border-radius:2px}

.site-footer{position:absolute;left:0;top:923px;width:1200px;height:80px;background:var(--footer-bg)}
.legal{position:absolute;left:131px;top:22px;font-size:12.6px;line-height:19px;color:var(--muted)}
.legal a{color:var(--muted);text-decoration:none}
.social{position:absolute;left:960px;top:25px;display:flex;gap:9px}
.social a{display:block;width:30px;height:30px;background:var(--social-blue);text-indent:-999px;overflow:hidden}
</style>
</head>
<body>

<header class="site-header">
  <div class="brand-name">Northline Diesel</div>
  <svg class="phone-icon" width="40" height="54" viewBox="0 0 40 54" aria-hidden="true">
    <path d="M12 2c-5 2-7 8-6 15 1 10 4 19 10 25 3 2 5 2 7 0l-4-8c-2 1-3 0-4-2-2-4-3-8-3-11 0-2 1-3 3-3L14 3z" fill="#222"/>
    <path d="M23 42c3 6 8 8 14 6" fill="none" stroke="#222" stroke-width="2"/>
  </svg>
  <div class="contact-block">
    <div>Contact us on <span class="phone">(02)5550 1234</span></div>
    <div>or email us <span class="email">info@northline.net</span></div>
  </div>
</header>

<div class="hero-band"></div>

<nav class="main-nav">
  <a href="#" style="left:187px">HOME</a>
  <a href="#" style="left:298px">WHAT WE DO</a>
  <a href="#" style="left:436px">HOW WE DO IT</a>
  <a href="#" style="left:562px">ABOUT US</a>
  <a href="#" style="left:686px">GUARANTEES</a>
  <a href="#" style="left:805px">RESULTS</a>
  <a href="#" style="left:912px">CONTACT</a>
  <a href="#" style="left:1008px">BLOG</a>
</nav>

<section class="slider">
  <div class="slide-photo" role="img" aria-label="White light commercial tray truck parked on gravel in front of trees and dry grass"></div>
  <div class="callout">
    <svg width="365" height="178" viewBox="0 0 365 178" aria-hidden="true" style="position:absolute;left:0;top:0">
      <polygon points="0,0 365,0 365,178 42,178" fill="var(--accent-blue)"/>
      <polygon points="10,0 365,0 365,170 48,170" fill="var(--callout-bg)"/>
    </svg>
    <div class="callout-text">
      We help diesel vehicle fleets
      <span class="save">save up to</span>
      <span class="big">20% <small>FUEL COSTS</small></span>
      <span class="tail">by optimising their engines.</span>
    </div>
  </div>
  <div class="partner-badge badge-member" role="img" aria-label="Industry association member badge"><span></span></div>
  <div class="partner-badge badge-partner" role="img" aria-label="Azure Tune partner badge"><span></span></div>
  <div class="slider-dots"><i class="active"></i><i></i><i></i></div>
</section>

<section class="features">
  <article class="feature" style="left:0">
    <h2>ABOUT US</h2>
    <p>Northline Diesel have combined over 50 years experience in all aspects of the automotive industry including commercial fleet and diesel engines. We are the ...</p>
    <a class="read-more" href="#">Read More</a>
  </article>
  <article class="feature" style="left:243px">
    <h2>WHAT WE DO</h2>
    <p>Northline Diesel delivers award winning, ISO 9001 certified diesel engine ECU remapping for fleet operations. As Principal Australian Fleet Agent for Azure Tune...</p>
    <a class="read-more" href="#">Read More</a>
  </article>
  <article class="feature" style="left:487px">
    <h2>HOW WE DO IT</h2>
    <p>Northline Diesel will conduct an obligation Free Consultation with your Fleet Representatives to determine your Fleets needs, and identify any customization...</p>
    <a class="read-more" href="#">Read More</a>
  </article>
  <article class="feature" style="left:731px">
    <h2>WHY</h2>
    <p>We've acted on customer requests for cost effective, financially attractive solutions to reduce fuel and operating costs whilst also reducing environmental foot...</p>
    <a class="read-more" href="#">Read More</a>
  </article>
</section>

<footer class="site-footer">
  <div class="legal">
    <div>Copyright 2014 Azure Tune. All Rights Reserved.</div>
    <div><a href="#">Privacy Policy</a> | <a href="#">Terms and Conditions</a></div>
  </div>
  <div class="social">
    <a href="#" aria-label="Pinnet">Pinnet</a>
    <a href="#" aria-label="Chirp">Chirp</a>
    <a href="#" aria-label="Linkwork">Linkwork</a>
  </div>
</footer>

</body>
</html>
```